Harbor Loom Floors Letterhead

Letterhead used for business reasons. It must be editable and easy to use.

Address is 2715 W. Pelican Lane Maple Bay OR 97233 - 503.382.6519

```html
<!DOCTYPE html>
<html lang="en">
<head>
<meta charset="utf-8">
<title>Harbor Loom Floors Letterhead</title>
<link href="https://fonts.googleapis.com/css2?family=Montserrat:wght@400;500;600&family=Dancing+Script:wght@600&display=swap" rel="stylesheet">
<style>
  :root {
    --backdrop: #e9e9ea;
    --paper: #ffffff;
    --brand-orange: #e08a24;
    --ink: #1d1d1d;
    --band-dark: #1b1b1b;
    --footer-text: #ffffff;
  }
  * { box-sizing: border-box; margin: 0; padding: 0; }
  html, body {
    width: 1200px; height: 874px; overflow: hidden;
    background: var(--backdrop);
    font-family: "Montserrat", Arial, sans-serif;
  }
  .letterhead {
    position: absolute; left: 310px; top: 27px;
    width: 580px; height: 820px;
    background: var(--paper);
    box-shadow: 0 4px 18px rgba(0,0,0,0.12);
    overflow: hidden;
    color: var(--ink);
  }
  .brand {
    position: absolute; left: 44px; top: 44px;
    display: flex; align-items: center; gap: 10px;
  }
  .brand-mark {
    width: 14px; height: 14px; border-radius: 50%;
    background: var(--brand-orange);
  }
  .brand-name {
    font-size: 26px; font-weight: 500; color: var(--brand-orange);
    letter-spacing: 0.5px;
  }
  .letter-body {
    position: absolute; left: 44px; top: 118px; width: 470px;
    font-size: 9.5px; line-height: 1.45;
  }
  .letter-date { margin-bottom: 14px; }
  .recipient { margin-bottom: 14px; }
  .recipient-company { margin-bottom: 18px; }
  .salutation { font-size: 13px; font-weight: 600; margin-bottom: 18px; }
  .paragraph { margin-bottom: 14px; }
  .sign-off { margin-top: 16px; }
  .signature {
    font-family: "Dancing Script", cursive;
    font-size: 30px; margin-top: 22px; margin-left: 20px;
  }
  .footer-rule {
    position: absolute; left: 0; right: 0; bottom: 78px;
    height: 4px; background: var(--brand-orange);
  }
  .footer-band {
    position: absolute; left: 0; right: 0; bottom: 0;
    height: 72px; background: var(--band-dark);
    display: flex; align-items: center; justify-content: flex-end;
    padding: 0 44px;
    color: var(--footer-text); font-size: 10px; line-height: 1.6;
  }
  .footer-contact { text-align: left; }
  .footer-contact .phone { display: flex; align-items: center; gap: 6px; }
  .footer-contact svg { width: 10px; height: 10px; }
</style>
</head>
<body>
  <main class="letterhead">
    <header class="brand">
      <span class="brand-mark"></span>
      <span class="brand-name">Harbor Loom Floors</span>
    </header>

    <section class="letter-body">
      <p class="letter-date">January-03-2020</p>
      <p class="recipient">Mr. Alan Reyes<br>President</p>
      <p class="recipient-company">Brightpath Company<br>123 Street Name, Suite# 10<br>City, State, 120023</p>
      <p class="salutation">Dear Mr, Alan</p>
      <p class="paragraph">Lorem ipsum dolor sit amet, consectetur adipiscing elit, sed do eiusmod tempor incididunt ut labore et dolore magna aliqua. Ut enim ad minim veniam, quis nostrud exercitation ullamco laboris nisi ut aliquip ex ea commodo consequat. Duis aute irure dolor in reprehenderit in voluptate velit esse cillum dolore eu fugiat nulla pariatur.</p>
      <p class="paragraph">Lorem ipsum dolor sit amet, consectetur adipiscing elit, sed do eiusmod tempor incididunt ut labore et dolore magna aliqua. Ut enim ad minim veniam, quis nostrud exercitation ullamco laboris nisi ut aliquip ex ea commodo consequat. Duis aute irure dolor in reprehenderit in voluptate velit esse cillum dolore eu fugiat nulla pariatur.</p>
      <p class="paragraph">Lorem ipsum dolor sit amet, consectetur adipiscing elit, sed do eiusmod tempor incididunt ut labore et dolore magna aliqua. Ut enim ad minim veniam, quis nostrud exercitation ullamco laboris nisi ut aliquip ex ea commodo consequat.</p>
      <p class="paragraph">Excepteur sint occaecat cupidatat non proident, sunt in culpa qui officia deserunt mollit anim id est laborum. re et dolore magnam aliquam quaerat voluptatem.</p>
      <p class="sign-off">Regards</p>
      <p class="signature">Daniel Hart</p>
    </section>

    <div class="footer-rule"></div>
    <footer class="footer-band">
      <div class="footer-contact">
        <p>2715 W. Pelican Lane</p>
        <p>Maple Bay OR 97233</p>
        <p class="phone">
          <svg viewBox="0 0 24 24" aria-hidden="true"><path fill="var(--brand-orange)" d="M6.6 10.8a15 15 0 0 0 6.6 6.6l2.2-2.2a1 1 0 0 1 1-.25 11.4 11.4 0 0 0 3.6.57 1 1 0 0 1 1 1V20a1 1 0 0 1-1 1A17 17 0 0 1 3 4a1 1 0 0 1 1-1h3.5a1 1 0 0 1 1 1c0 1.25.2 2.45.57 3.57a1 1 0 0 1-.25 1z"/></svg>
          503.382.6519
        </p>
      </div>
    </footer>
  </main>
</body>
</html>
```